Venture Capital Firm Needs Website Redesign

We need a bold revamp of our website (https://halverine.vc/)
which at the moment looks washed out. We want a crisp, fresh and unique look. Feel free to keep as much or as little content in the site. The only thing we need to keep is a team section. The site should convey a clear distinction between our 3 product lines: Venture Capital, Private Credit, and Crypto. Two versions of our logo are attached and they should not change. For design inspirations, we like http://www.9plm.com/ for a more simple site and for a more built out site we like http://bluetorch.com/

Updates
Industry/Entity Type
Investment
Coding
Coded - Design and coding required
Number of Pages Required
1 page
Font styles to use
Colors
Designer to choose colors to be used in the design.
Requirements
Must have
- - Clear distinction between our 3 product lines: Venture Capital, Private Credit
- - Team section

Nice to have
- Some really creative aspect like http://www.9plm.com/ has with the distinction between first, second, and third kind

```html
<!DOCTYPE html>
<html lang="en">
<head>
<meta charset="utf-8">
<title>Halverine</title>
<link href="https://fonts.googleapis.com/css2?family=Lato:wght@300;400;700;900&family=Raleway:wght@300;400&display=swap" rel="stylesheet">
<style>
:root{
  --green:#7c9a2f;
  --green-soft:#8ea83d;
  --ink:#1f1f1f;
  --text:#3a3a3a;
  --muted:#6b6b6b;
  --line:#dedede;
  --panel:#f1f1f1;
  --footer:#2f2f2f;
  --white:#ffffff;
}
*{margin:0;padding:0;box-sizing:border-box}
html,body{width:1200px;height:3422px;overflow:hidden;background:var(--white)}
body{position:relative;font-family:'Lato',sans-serif;color:var(--text)}
.abs{position:absolute}

/* header */
.site-header{position:absolute;left:0;top:0;width:1200px;height:96px;background:var(--white)}
.brand{position:absolute;left:75px;top:28px;display:flex;align-items:center;gap:10px;font-family:'Raleway',sans-serif;font-weight:300;font-size:40px;letter-spacing:1px;color:var(--ink)}
.brand-dot{width:14px;height:14px;border-radius:50%;background:var(--green)}
.nav a{position:absolute;top:38px;font-size:17px;color:var(--ink);text-decoration:none}
.menu-icon{position:absolute;left:1100px;top:40px;width:26px}
.menu-icon span{display:block;height:3px;background:var(--green);margin-bottom:5px}

/* hero */
.hero{position:absolute;left:0;top:96px;width:1200px;height:524px;clip-path:polygon(0 0,100% 0,100% 100%,0 88%);
  background:linear-gradient(135deg,#5a4a3a 0%,#8b7a66 35%,#bfb3a3 55%,#7d6c58 80%,#4b3d30 100%)}
.hero-shade{position:absolute;inset:0;background:rgba(20,15,10,.35)}
.hero h1{position:absolute;left:0;top:180px;width:1200px;text-align:center;color:var(--white);font-weight:700;font-size:33px;line-height:42px}
.chevron{position:absolute;left:584px;top:440px}

/* about */
.about-label{left:75px;top:665px;font-size:36px;font-weight:700;color:var(--ink)}
.about-brand{left:75px;top:708px;display:flex;align-items:center;gap:12px;font-family:'Raleway',sans-serif;font-weight:300;font-size:54px;color:var(--ink);letter-spacing:1px}
.about-brand .brand-dot{width:18px;height:18px}
.about-copy{left:75px;top:782px;width:1050px;font-size:17px;line-height:32px;color:var(--text)}
.divider{left:75px;top:967px;width:1050px;height:1px;background:var(--line)}

/* product sections */
.section-title{font-size:36px;font-weight:700;color:var(--ink)}
.section-copy{font-size:14px;line-height:30px;color:var(--text)}
.partner{font-size:22px;font-weight:700;color:var(--ink);display:flex;align-items:center;gap:8px}
.partner i{display:inline-block;width:12px;height:12px;background:var(--green)}
.crypto-visual{left:8px;top:1875px;width:535px;height:290px;border-radius:8px;background:linear-gradient(180deg,#e6e6e6 0%,#f7f7f7 50%,#cfcfcf 100%)}

/* team */
.team{left:0;top:2235px;width:1200px;height:548px;background:var(--panel)}
.block-title{position:absolute;left:0;width:1200px;text-align:center;font-size:36px;font-weight:700;color:var(--ink)}
.block-sub{position:absolute;left:0;width:1200px;text-align:center;font-size:17px;color:var(--green)}
.card{position:absolute;top:153px;width:242px;height:326px;background:var(--white);text-align:center}
.card .photo{margin:16px auto 0;width:210px;height:196px;background:linear-gradient(180deg,#bdbdbd,#7d7d7d)}
.card .name{margin-top:18px;font-size:19px;font-weight:700;color:var(--green)}
.card .role{margin-top:4px;font-size:13px;color:var(--ink)}
.card .links{margin-top:8px;font-size:12px;font-weight:700;color:var(--ink);letter-spacing:.5px}
.arrow{position:absolute;top:300px}

/* contact */
.contact-mark{left:555px;top:2957px;width:90px;height:90px;border:2px solid var(--ink);border-radius:50%}
.contact-brand{left:0;top:3048px;width:1200px;display:flex;justify-content:center;align-items:center;gap:10px;font-family:'Raleway',sans-serif;font-weight:300;font-size:42px;color:var(--ink);letter-spacing:1px}
.contact-line{left:0;width:1200px;text-align:center;font-size:19px;color:var(--ink)}

/* footer */
.site-footer{left:0;top:3244px;width:1200px;height:178px;background:var(--footer)}
.site-footer .copy{position:absolute;left:0;top:60px;width:1200px;text-align:center;font-size:13px;color:#cfcfcf}
.site-footer .social{position:absolute;left:0;top:95px;width:1200px;text-align:center;font-size:14px;color:var(--white);letter-spacing:1px}
</style>
</head>
<body>

<header class="site-header">
  <div class="brand"><span class="brand-dot"></span>HALVERINE</div>
  <nav class="nav">
    <a style="left:598px" href="#vc">Venture Capital</a>
    <a style="left:776px" href="#credit">Private Credit</a>
    <a style="left:940px" href="#crypto">Crypto</a>
  </nav>
  <div class="menu-icon"><span></span><span></span><span></span></div>
</header>

<section class="hero" role="img" aria-label="Team members working over printed financial charts on a desk">
  <div class="hero-shade"></div>
  <h1>Halverine operates at the intersection of technology<br>and novel asset classes.</h1>
  <svg class="chevron" width="32" height="20" viewBox="0 0 32 20"><polyline points="3,3 16,16 29,3" fill="none" stroke="#fff" stroke-width="4"/></svg>
</section>

<h2 class="abs about-label">About</h2>
<div class="abs about-brand"><span class="brand-dot"></span>HALVERINE</div>
<p class="abs about-copy">Halverine operates three businesses that bridge technology and finance. We invest in pre-seed venture capital, and build software for the companies we invest in. We manage direct private credit funds that provide private credit capital to alternative private credit platforms, enabling them to finance the loans they originate. We create crypto funds for individuals, IRAs and institutions to get simple and easy access to cryptocurrencies.</p>
<div class="abs divider"></div>

<!-- Venture Capital -->
<svg class="abs" style="left:0;top:1010px" width="590" height="409" viewBox="0 0 590 409">
  <path d="M0,95 Q60,0 140,0 Q170,0 190,30 L580,409 L0,409 Z" fill="var(--green)"/>
</svg>
<div class="abs" style="left:100px;top:1075px;width:170px;height:330px;border-radius:12px;background:linear-gradient(180deg,#d9d2b8 0%,#f2d64b 60%,#e6c23a 100%)" role="img" aria-label="Hand dropping a coin into a glowing light bulb"></div>
<h2 class="abs section-title" id="vc" style="left:502px;top:1042px">Venture Capital</h2>
<p class="abs section-copy" style="left:502px;top:1098px;width:630px">We invest in early-stage startups led by founders who are passionate and knowledgeable about the markets they serve. We have our own software developers and product managers. We work with the founders in our portfolio to help them bring products to market, earning equity for this work and for the cash we invest in their companies.</p>
<div class="abs partner" style="left:502px;top:1255px;font-size:15px"><i></i>Northgate</div>
<div class="abs partner" style="left:660px;top:1255px;font-size:15px"><i></i>tinyloop</div>
<div class="abs partner" style="left:768px;top:1252px">playpath</div>
<div class="abs partner" style="left:900px;top:1252px;font-size:19px">BoardLine</div>

<!-- Private Credit -->
<svg class="abs" style="left:620px;top:1419px" width="580" height="406" viewBox="0 0 580 406">
  <path d="M0,406 L450,20 Q480,0 510,0 Q560,0 580,40 L580,406 Z" fill="var(--green)"/>
</svg>
<div class="abs" style="left:870px;top:1495px;width:260px;height:330px;border-radius:12px;background:linear-gradient(160deg,#f2d64b 0%,#d9d2b8 55%,#4c8a3a 100%)" role="img" aria-label="Hands exchanging a light bulb and a stack of banknotes"></div>
<h2 class="abs section-title" id="credit" style="left:75px;top:1462px">Private Credit</h2>
<p class="abs section-copy" style="left:75px;top:1514px;width:720px">Halverine Private Credit provides capital to lending businesses that are focused on using technology to establish new credit markets, create new credit products or dramatically re-invent an existing form of credit. We believe that the pioneers who build something truly different in a credit market will create the most sustainable business models. Given our heritage as a venture firm, we are comfortable with emerging businesses and can provide capital for a company's first loan.</p>
<div class="abs partner" style="left:80px;top:1712px;font-size:26px;font-weight:900"><i></i>Teralend</div>
<div class="abs" style="left:285px;top:1682px;width:60px;height:80px;border-radius:50%;background:linear-gradient(180deg,#7cbf3a 0%,#5a4a3a 100%)" role="img" aria-label="Partner badge"></div>
<div class="abs partner" style="left:434px;top:1716px;font-size:20px;font-weight:400;letter-spacing:1px">BRIGHTFUND</div>

<!-- Crypto -->
<svg class="abs" style="left:0;top:1825px" width="580" height="410" viewBox="0 0 580 410">
  <path d="M0,60 Q20,0 80,0 Q110,0 130,20 L570,410 L0,410 Z" fill="var(--green)"/>
</svg>
<div class="abs crypto-visual" role="img" aria-label="Laptop showing the index growth chart"></div>
<h2 class="abs section-title" id="crypto" style="left:570px;top:1918px">Crypto</h2>
<p class="abs section-copy" style="left:570px;top:1974px;width:560px">The Halverine Crypto Index tracks the top 15 cryptocurrencies weighted by market cap and rebalanced twice a month. We believe this is the simplest and most cost effective way to obtain cryptocurrency exposure. Our process has been designed by experts from financial services and cryptocurrency industries.</p>

<!-- Team -->
<section class="abs team">
  <h2 class="block-title" style="top:46px">Our Team</h2>
  <p class="block-sub" style="top:101px">We would love to hear from you</p>
  <svg class="arrow" style="left:44px" width="16" height="26" viewBox="0 0 16 26"><polyline points="13,3 3,13 13,23" fill="none" stroke="#222" stroke-width="4"/></svg>
  <div class="card" style="left:75px"><div class="photo" role="img" aria-label="Portrait of team partner"></div><div class="name">Omar Rashid</div><div class="role">Partner</div><div class="links">Profile · Connect</div></div>
  <div class="card" style="left:344px"><div class="photo" role="img" aria-label="Portrait of team partner"></div><div class="name">Devan Mirpuri</div><div class="role">Partner</div><div class="links">Profile · Connect</div></div>
  <div class="card" style="left:614px"><div class="photo" role="img" aria-label="Portrait of team partner"></div><div class="name">Karim Sollah</div><div class="role">Partner</div><div class="links">Profile · Connect</div></div>
  <div class="card" style="left:883px"><div class="photo" role="img" aria-label="Portrait of team partner"></div><div class="name">Weston Crane</div><div class="role">Partner</div><div class="links">Profile · Connect</div></div>
  <svg class="arrow" style="left:1140px" width="16" height="26" viewBox="0 0 16 26"><polyline points="3,3 13,13 3,23" fill="none" stroke="#222" stroke-width="4"/></svg>
</section>

<!-- Contact -->
<h2 class="block-title" style="top:2846px">Contact Us</h2>
<p class="block-sub" style="top:2900px">We would love to hear from you</p>
<div class="abs contact-mark"></div>
<div class="abs contact-brand">HALVERINE</div>
<p class="abs contact-line" style="top:3115px">218 Marlow Street, Suite 604 New York, NY 10012</p>
<p class="abs contact-line" style="top:3152px">
  <svg width="18" height="14" viewBox="0 0 18 14" style="vertical-align:-1px;margin-right:10px"><rect x="0" y="0" width="18" height="14" rx="1" fill="var(--green)"/><polyline points="1,1 9,8 17,1" fill="none" stroke="#fff" stroke-width="1.6"/></svg>info@halverine.vc
</p>

<footer class="abs site-footer">
  <p class="copy">Copyright © 2018 Company Name. All Right Reserved</p>
  <p class="social">Feed · Post · Photo · Network · Video</p>
</footer>

</body>
</html>
```